Merry Meadow Roasters

We need a website to sell coffee with a horse theme. We already have a logo and have designed 4 different coffee bags/flavors so far, each of which will be available in ground or whole bean. The brand is intended to be light hearted/whimsical.

Requirements
Must have
• incorporation of attached photos
Nice to have
• underlying background theme with sky/grass

```html
<!DOCTYPE html>
<html lang="en">
<head>
<meta charset="utf-8">
<title>Merry Meadow Roasters</title>
<link rel="stylesheet" href="https://fonts.googleapis.com/css2?family=Montserrat:wght@700;800&family=Ubuntu:wght@500;700&family=Roboto:wght@400;500&family=Poppins:wght@400;600&display=swap">
<style>
:root{
  --tan:#e6c9a0;
  --sand:#f4d8b6;
  --peach:#f9e9df;
  --peach-deep:#f3d3b5;
  --ink:#1f1f1f;
  --text:#333;
  --muted:#8a8a8a;
  --star:#f2a51a;
  --dark:#1e1e1e;
  --line:#dcdcdc;
  --white:#fff;
}
*{margin:0;padding:0;box-sizing:border-box}
html,body{width:1200px;height:3617px;overflow:hidden}
body{position:relative;font-family:"Roboto",sans-serif;color:var(--text);background:var(--white)}
.abs{position:absolute}
.btn{position:absolute;display:flex;align-items:center;justify-content:center;background:var(--sand);color:var(--ink);font-family:"Ubuntu",sans-serif;font-weight:500;font-size:16px}
.art{position:absolute}

/* top bar */
.topbar{top:0;left:0;width:1200px;height:42px;background:var(--tan);color:var(--white);font-size:14px}
.social{left:110px;top:14px;display:flex;gap:14px}
.social span{width:15px;height:15px;border-radius:50%;background:var(--white);display:block}
.topbar .info{top:12px;display:flex;align-items:center;gap:10px}
.topbar b{font-weight:500}

/* nav */
.nav{top:42px;left:0;width:1200px;height:78px;background:var(--white);font-family:"Ubuntu",sans-serif;font-weight:500;font-size:15px;color:var(--ink)}
.nav a{position:absolute;top:31px;color:inherit;text-decoration:none}
.logo{left:523px;top:45px;width:156px;height:138px;border-radius:0 0 78px 78px;background:var(--peach-deep);z-index:5;display:flex;align-items:flex-start;justify-content:center;padding-top:4px}
.logo-inner{width:134px;height:124px;border-radius:0 0 67px 67px;background:var(--white);display:flex;align-items:center;justify-content:center;text-align:center;font-family:"Ubuntu",sans-serif;font-weight:700;font-size:17px;line-height:1.15;color:var(--ink)}
.badge{position:absolute;left:1071px;top:22px;width:15px;height:15px;border-radius:50%;background:var(--star);font-size:9px;color:var(--ink);display:flex;align-items:center;justify-content:center}

/* hero */
.hero{top:120px;left:0;width:1200px;height:597px;background:linear-gradient(180deg,#b9772f 0%,#e4a955 22%,#8d7a3c 45%,#4f5a25 62%,#5a4126 82%,#3a2616 100%)}
.hero-copy{left:110px;top:120px;color:var(--white)}
.hero-copy .kicker{font-family:"Montserrat",sans-serif;font-weight:700;font-size:30px;letter-spacing:.5px}
.hero-copy h1{font-family:"Montserrat",sans-serif;font-weight:800;font-size:66px;line-height:76px;margin-top:4px}
.hero-copy p{font-size:15.5px;line-height:31px;width:470px;margin-top:10px}

/* about */
.about{top:717px;left:0;width:1200px;height:631px;background:var(--peach)}
.about h2{left:632px;top:142px;font-family:"Ubuntu",sans-serif;font-weight:500;font-size:31px;color:var(--ink)}
.about p{left:632px;top:195px;width:455px;font-size:14.8px;line-height:29.2px;color:#444}

/* products */
.section-title{position:absolute;left:0;width:1200px;text-align:center;font-family:"Ubuntu",sans-serif;color:var(--ink)}
.card{position:absolute;top:1605px;width:223px;height:358px;background:var(--white);border:1.5px solid #ececec;border-radius:4px 30px 30px 30px;box-shadow:6px 8px 12px rgba(0,0,0,.12);text-align:center}
.bag{position:absolute;top:-52px;left:41px;width:140px;height:226px;background:linear-gradient(180deg,#f1ede6 0%,#e4ddd0 55%,#7a5532 72%,#161312 100%);border-radius:3px}
.card .price{position:absolute;top:204px;width:100%;font-size:15px;color:var(--ink)}
.card .name{position:absolute;top:231px;width:100%;font-family:"Ubuntu",sans-serif;font-weight:500;font-size:16px;color:var(--ink)}
.card .stars{position:absolute;top:255px;width:100%;font-size:12px;color:var(--star);letter-spacing:1px}
.card .btn{left:34px;top:290px;width:154px;height:35px;border-radius:18px;font-size:15px;background:linear-gradient(180deg,#f6dfc2,#ecc89c)}

/* dark band */
.brew{top:2075px;left:0;width:1200px;height:499px;background:radial-gradient(ellipse at 50% 30%,#3a3a3a 0%,#1d1d1d 70%)}
.beans{left:0;top:2372px;width:1200px;height:202px;background:linear-gradient(180deg,rgba(29,29,29,0) 0%,#6b3f22 35%,#4a2a16 70%,#2b180c 100%)}
.brew-copy{top:2165px;left:0;width:1200px;text-align:center;color:var(--white)}
.brew-copy h2{font-family:"Ubuntu",sans-serif;font-weight:700;font-size:40px}
.brew-copy p{width:860px;margin:14px auto 0;font-size:14.8px;line-height:28px;color:#e6e6e6}

/* testimonials */
.rule{position:absolute;height:2px;background:var(--tan)}
.tcard{position:absolute;width:311px;height:339px;background:#f8f8f8;border:1.5px solid var(--line);font-family:"Poppins",sans-serif;padding:36px 16px 0 16px}
.tcard .t-stars{color:var(--star);font-size:18px;letter-spacing:1px}
.tcard p{font-size:15px;line-height:27.4px;color:#333;margin-top:12px}
.who{position:absolute;left:18px;bottom:22px;display:flex;align-items:center;gap:14px}
.avatar{width:62px;height:62px;border-radius:50%;background:linear-gradient(180deg,#c9b8a6,#6d5a4b)}
.who b{display:block;font-weight:600;font-size:15.5px;color:var(--ink)}
.who small{font-size:13.5px;color:var(--muted)}

/* footer */
.footer{top:3225px;left:0;width:1200px;height:392px;background:var(--dark);color:var(--white)}
.fcol{position:absolute;top:45px}
.fcol h4{font-weight:400;font-size:17px;text-transform:uppercase}
.fcol h4::after{content:"";display:block;width:42px;height:2px;background:var(--tan);margin-top:10px}
.fcol ul{list-style:none;margin-top:20px}
.fcol li{font-size:16.5px;line-height:30.6px}
.contact li{display:flex;gap:14px;align-items:flex-start}
.contact svg{margin-top:8px;flex:none}
.cards{display:flex;gap:8px;margin-top:20px}
.cards span{width:44px;height:26px;border-radius:3px;background:var(--white);color:#1a3d8f;font-size:9px;font-weight:500;display:flex;align-items:center;justify-content:center}
.copyright{position:absolute;left:0;top:345px;width:1200px;text-align:center;font-size:16.5px}
</style>
</head>
<body>

<header class="abs topbar">
  <div class="abs social" aria-label="Social links"><span></span><span></span><span></span><span></span></div>
  <div class="abs info" style="left:540px">
    <svg width="16" height="12" viewBox="0 0 16 12"><rect width="16" height="12" rx="1" fill="#fff"/><path d="M1 1l7 5 7-5" stroke="#e6c9a0" stroke-width="1.5" fill="none"/></svg>
    <span><b>Email:</b> info@merrymeadowroasters.com</span>
  </div>
  <div class="abs info" style="left:874px">
    <svg width="14" height="14" viewBox="0 0 24 24"><path fill="#fff" d="M6.6 10.8a15 15 0 006.6 6.6l2.2-2.2a1 1 0 011-.25 11.4 11.4 0 003.6.57 1 1 0 011 1V20a1 1 0 01-1 1A17 17 0 013 4a1 1 0 011-1h3.5a1 1 0 011 1c0 1.25.2 2.45.57 3.57a1 1 0 01-.25 1z"/></svg>
    <span><b>Phone:</b> +1 555 0100 2020</span>
  </div>
</header>

<nav class="abs nav">
  <a style="left:111px">Home</a>
  <a style="left:200px">About Us</a>
  <a style="left:313px">Our Products</a>
  <a style="left:780px">Testimonials</a>
  <a style="left:907px">Contact Us</a>
  <svg class="abs" style="left:1014px;top:32px" width="17" height="17" viewBox="0 0 20 20"><circle cx="8" cy="8" r="6" stroke="#222" stroke-width="1.8" fill="none"/><path d="M12.5 12.5L18 18" stroke="#222" stroke-width="1.8"/></svg>
  <svg class="abs" style="left:1050px;top:30px" width="22" height="20" viewBox="0 0 22 20"><path d="M1 2h3l2.5 11h11l2-8H6" stroke="#222" stroke-width="1.8" fill="none"/><circle cx="8" cy="17" r="1.6" fill="#222"/><circle cx="16" cy="17" r="1.6" fill="#222"/></svg>
  <span class="badge">0</span>
</nav>
<div class="abs logo"><div class="logo-inner">Merry Meadow<br>Roasters</div></div>

<section class="abs hero" role="img" aria-label="Coffee plantation hills at sunset with a cup of coffee, a burlap sack of beans and a cartoon horse rider">
  <div class="abs hero-copy">
    <div class="kicker">WELCOME TO</div>
    <h1>MERRY MEADOW<br>ROASTERS</h1>
    <p>Duis aute irure dolor in reprehenderit in voluptate velit esse cillum dolore eu fugiat nulla pariatur.</p>
  </div>
  <a class="btn" style="left:110px;top:408px;width:133px;height:47px">Shop Now</a>
</section>

<section class="abs about">
  <div class="abs" style="left:108px;top:116px;width:177px;height:143px;background:var(--peach-deep)"></div>
  <div class="abs" style="left:225px;top:214px;width:347px;height:282px;background:var(--peach-deep)"></div>
  <div class="art" role="img" aria-label="Cup of coffee with heart-shaped steam beside a scoop of roasted beans" style="left:118px;top:126px;width:444px;height:360px;background:radial-gradient(ellipse at 50% 60%,#a98462 0%,#5a3a22 45%,#2a1a10 100%)"></div>
  <h2 class="abs">About Us</h2>
  <p class="abs">Lorem ipsum dolor sit amet, consectetur adipiscing elit, sed do eiusmod tempor incididunt ut labore et dolore magna aliqua. Ut enim ad minim veniam, quis nostrud exercitation ullamco laboris nisi ut aliquip ex ea commodo consequat. Duis aute irure dolor in reprehenderit in voluptate velit esse cillum dolore eu fugiat nulla pariatur. Excepteur sint occaecat cupidatat non proident, sunt in culpa qui officia deserunt mollit anim id est laborum.</p>
  <a class="btn" style="left:632px;top:421px;width:133px;height:47px">Read More</a>
</section>
<div class="art" role="img" aria-label="Cartoon rider on a horse jumping a show fence" style="left:892px;top:1144px;width:218px;height:246px;background:linear-gradient(180deg,#e8d3b4 0%,#c99a66 60%,#5577a0 100%);border-radius:40% 40% 8px 8px;opacity:.85"></div>

<div class="art" role="img" aria-label="Cartoon cowboy riding a bucking horse" style="left:7px;top:1425px;width:133px;height:155px;background:linear-gradient(180deg,#e9dccd,#8a4a2a);border-radius:45%;opacity:.85"></div>
<h2 class="section-title" style="top:1444px;font-weight:500;font-size:34px">Our Products</h2>

<article class="card" style="left:110px"><div class="bag" role="img" aria-label="Bucking Bean coffee bag"></div><div class="price">$ 50.00</div><div class="name">Bucking Bean</div><div class="stars">★★★★☆</div><a class="btn">Shop Now</a></article>
<article class="card" style="left:362px"><div class="bag" role="img" aria-label="Prancing Pony coffee bag"></div><div class="price">$ 50.00</div><div class="name">Prancing Pony</div><div class="stars">★★★★☆</div><a class="btn">Shop Now</a></article>
<article class="card" style="left:614px"><div class="bag" role="img" aria-label="Timber Trot Blend coffee bag"></div><div class="price">$ 50.00</div><div class="name">Timber Trot Blend</div><div class="stars">★★★★☆</div><a class="btn">Shop Now</a></article>
<article class="card" style="left:866px"><div class="bag" role="img" aria-label="Turn N Gallop coffee bag"></div><div class="price">$ 50.00</div><div class="name">Turn N Gallop</div><div class="stars">★★★★☆</div><a class="btn">Shop Now</a></article>

<section class="abs brew" role="img" aria-label="Dark coffee bean texture with a pile of roasted beans along the bottom"></section>
<div class="art beans" role="img" aria-label="Heap of roasted coffee beans"></div>
<div class="abs brew-copy">
  <h2>Galloping into Your Morning Brew.</h2>
  <p>Duis aute irure dolor in reprehenderit in voluptate velit esse cillum dolore eu fugiat nulla pariatur. Excepteur sint occaecat cupidatat non proident, sunt in culpa qui officia deserunt mollit anim id est laborum.Lorem ipsum dolor sit amet, consectetur adipiscing elit, sed do eiusmod tempor incididunt ut labore et dolore magna aliqua.</p>
</div>
<a class="btn" style="left:527px;top:2347px;width:133px;height:47px">Read More</a>
<div class="art" role="img" aria-label="Cartoon rider on a grey horse" style="left:1018px;top:2036px;width:182px;height:210px;background:linear-gradient(180deg,#c9d6e2,#8e9aa6 60%,#caa77a);border-radius:45% 10% 20% 40%;opacity:.9"></div>

<div class="art" role="img" aria-label="Cartoon rider jumping a fence" style="left:7px;top:2626px;width:131px;height:147px;background:linear-gradient(180deg,#eadcc8,#b98a5c 60%,#5577a0);border-radius:40%;opacity:.85"></div>
<h2 class="section-title" style="top:2655px;font-weight:700;font-size:31px">Client Testimonials</h2>
<div class="rule" style="left:580px;top:2706px;width:40px"></div>

<article class="tcard" style="left:98px;top:2732px">
  <div class="t-stars">★★★★★</div>
  <p>Temporibus autem quibusdam et aut officiis debitis aut rerum neus saepe facere mus, onis voluptas eveniet ut et voluptates repudae sint et molestiae non lorem recusadae.</p>
  <div class="who"><div class="avatar" role="img" aria-label="Customer portrait"></div><div><b>Owen Hartley</b><small>United States</small></div></div>
</article>
<article class="tcard" style="left:441px;top:2770px;background:#fff;border-color:#eee;box-shadow:0 4px 14px rgba(0,0,0,.08)">
  <div class="t-stars">★★★★★</div>
  <p>Itaque earum rerum hic tenetur a sapiene delectus, ut aut reiciels volupatibus maiores alias conse uatur aut perferndis doloribus asperiores reiciendis voluptatbus repellat</p>
  <div class="who"><div class="avatar" role="img" aria-label="Customer portrait"></div><div><b>Lina</b><small>United States</small></div></div>
</article>
<article class="tcard" style="left:781px;top:2732px">
  <div class="t-stars">★★★★★</div>
  <p>At vero eos et accusamus et iusto odio dignissimos ducimus qui blaiis praesentium volupttum deleniti atque corrupti quos dolores et quas occaecati cupie non provident</p>
  <div class="who"><div class="avatar" role="img" aria-label="Customer portrait"></div><div><b>Marcus Dell</b><small>United States</small></div></div>
</article>
<article class="tcard" style="left:1129px;top:2775px">
  <div class="t-stars">★★★★★</div>
  <p>At vero eos et accusamus et iusto odio dignissimos ducimus qui blaiis praesentium volupttum deleniti atque corrupti quos dolores et quas occaecati cupie non provident</p>
  <div class="who"><div class="avatar" role="img" aria-label="Customer portrait"></div><div><b>Marcus Dell</b><small>United States</small></div></div>
</article>

<footer class="abs footer">
  <div class="fcol" style="left:115px"><h4>Quick Links</h4><ul><li>Home</li><li>About</li><li>Services</li><li>Products</li><li>Contact Us</li></ul></div>
  <div class="fcol" style="left:304px"><h4>Extras</h4><ul><li>Our Brands</li><li>Special Offers</li><li>Gift Vouchers</li><li>Affiliates</li></ul></div>
  <div class="fcol contact" style="left:537px"><h4>Contact Us</h4><ul>
    <li><svg width="13" height="13" viewBox="0 0 14 14"><circle cx="7" cy="7" r="5.8" stroke="#fff" stroke-width="1.6" fill="none"/><path d="M7 3.5V7h2.5" stroke="#fff" stroke-width="1.4" fill="none"/></svg><span>Monday - Friday: 09:00 - 18:30</span></li>
    <li><svg width="13" height="14" viewBox="0 0 12 16"><path d="M6 0a6 6 0 016 6c0 4.5-6 10-6 10S0 10.5 0 6a6 6 0 016-6z" fill="#fff"/><circle cx="6" cy="6" r="2.2" fill="#1e1e1e"/></svg><span style="width:240px">123 Meadowlark Lane, demo address</span></li>
    <li><svg width="13" height="13" viewBox="0 0 24 24"><path fill="#fff" d="M6.6 10.8a15 15 0 006.6 6.6l2.2-2.2a1 1 0 011-.25 11.4 11.4 0 003.6.57 1 1 0 011 1V20a1 1 0 01-1 1A17 17 0 013 4a1 1 0 011-1h3.5a1 1 0 011 1c0 1.25.2 2.45.57 3.57a1 1 0 01-.25 1z"/></svg><span>+1-555-010-2040</span></li>
    <li><svg width="14" height="11" viewBox="0 0 16 12"><rect x=".8" y=".8" width="14.4" height="10.4" rx="1" stroke="#fff" stroke-width="1.4" fill="none"/><path d="M1 1.5l7 5 7-5" stroke="#fff" stroke-width="1.4" fill="none"/></svg><span>shop@merrymeadowroasters.com</span></li>
  </ul></div>
  <div class="fcol" style="left:906px"><h4>Payment Options</h4><div class="cards"><span>Crestline</span><span>Paywise</span><span>Orbit</span></div></div>
  <div class="abs" style="left:110px;top:320px;width:980px;height:1px;background:#444"></div>
  <div class="copyright">© 2025 Merry Meadow Roasters. All Rights Reserved.</div>
</footer>

</body>
</html>
```